Communication and Marketing agency needs a new presentation card

We are a group of communication and marketing agencies specialized in companies that are in the logistics and industrial sector. The head agency is TELVANO Grupo and the group consists of 4 agencies: TELVANO Media, TELVANO Digital, TELVANO Research and DifundeEnPantalla. We hace 4 offices in Spain (Madrid, Barcelona, Valencia and Murcia). We are looking for a clean and attractive design that transmits our experience, brand presence in the market and knowledge to those who receive the card.It has to maintain the colors of the logo that is attached.
Target Market(s)
logistics and industrial sector
Marketing department
Contact Information for Business Card
Clean and attractive design

```html
<!DOCTYPE html>
<html lang="en">
<head>
<meta charset="utf-8">
<title>DifundeEnPantalla – Business Card</title>
<link rel="stylesheet" href="https://fonts.googleapis.com/css2?family=Questrial&display=swap">
<style>
  :root {
    --brand-red: #b8202e;
    --band-grey: #8a8b8d;
    --fold-grey: #5d5e60;
    --panel-light: #fbfbfb;
    --panel-edge: #e3e4e6;
    --ink-white: #ffffff;
  }
  * { margin: 0; padding: 0; box-sizing: border-box; }
  html, body {
    width: 1200px; height: 686px; overflow: hidden;
    background: #ffffff;
  }
  .card {
    position: relative;
    width: 1200px; height: 686px;
    font-family: "Questrial", "Century Gothic", sans-serif;
    overflow: hidden;
  }
  .brand-panel {
    position: absolute; left: 0; top: 0;
    width: 600px; height: 686px;
    background: radial-gradient(ellipse at 50% 50%, var(--panel-light) 0%, #f3f3f4 55%, var(--panel-edge) 100%);
  }
  .brand-name {
    position: absolute; left: 0; width: 600px; top: 305px;
    text-align: center;
    font-size: 54px; line-height: 1;
    color: var(--brand-red);
    letter-spacing: 0.5px;
  }
  .contact-panel {
    position: absolute; left: 600px; top: 0;
    width: 600px; height: 686px;
    background: var(--brand-red);
  }
  .name-band {
    position: absolute; left: 572px; top: 127px;
    width: 628px; height: 110px;
    background: var(--band-grey);
  }
  .band-fold {
    position: absolute; left: 572px; top: 237px;
    width: 28px; height: 19px;
  }
  .person-name {
    position: absolute; left: 737px; top: 140px;
    font-size: 46px; line-height: 1;
    color: var(--ink-white);
  }
  .person-role {
    position: absolute; left: 739px; top: 192px;
    font-size: 34px; line-height: 1;
    color: var(--ink-white);
  }
  .contact-list { list-style: none; }
  .contact-item {
    position: absolute; left: 699px;
    display: flex; align-items: flex-start;
    color: var(--ink-white);
    font-size: 32px; line-height: 40px;
  }
  .contact-item svg {
    width: 26px; height: 26px; margin-top: 7px; margin-right: 22px;
    flex: none;
  }
  .item-phone { top: 268px; }
  .item-email { top: 330px; }
  .item-web { top: 392px; }
  .item-address { top: 454px; }
</style>
</head>
<body>
<div class="card">
  <section class="brand-panel">
    <div class="brand-name">DifundeEnPantalla</div>
  </section>

  <section class="contact-panel" role="img" aria-label="Red panel with a faint geometric pattern"></section>

  <div class="name-band"></div>
  <svg class="band-fold" viewBox="0 0 28 19" aria-hidden="true">
    <polygon points="0,0 28,0 28,19" fill="var(--fold-grey)"/>
  </svg>
  <div class="person-name">Marcos Ibarra</div>
  <div class="person-role">Director</div>

  <ul class="contact-list">
    <li class="contact-item item-phone">
      <svg viewBox="0 0 26 26" aria-hidden="true">
        <rect x="9" y="1" width="13" height="24" rx="2.5" fill="none" stroke="#fff" stroke-width="2.4"/>
        <line x1="13" y1="21" x2="18" y2="21" stroke="#fff" stroke-width="2"/>
        <path d="M2 12 q0 -3 3 -3 h5 v12 h-5 q-3 0 -3 -3 z" fill="#fff"/>
      </svg>
      <span>0511 47 68902</span>
    </li>
    <li class="contact-item item-email">
      <svg viewBox="0 0 26 26" aria-hidden="true">
        <rect x="2" y="5" width="22" height="16" fill="none" stroke="#fff" stroke-width="2"/>
        <polyline points="2,5 13,15 24,5" fill="none" stroke="#fff" stroke-width="2"/>
      </svg>
      <span>Info@difundepantalla.com</span>
    </li>
    <li class="contact-item item-web">
      <svg viewBox="0 0 26 26" aria-hidden="true">
        <circle cx="13" cy="13" r="11" fill="#fff"/>
        <rect x="3" y="11" width="20" height="4" fill="var(--brand-red)"/>
      </svg>
      <span>www.difundepantalla.com</span>
    </li>
    <li class="contact-item item-address">
      <svg viewBox="0 0 26 26" aria-hidden="true">
        <path d="M13 3 a6 6 0 0 1 6 6 c0 4 -6 10 -6 10 c0 0 -6 -6 -6 -10 a6 6 0 0 1 6 -6 z" fill="none" stroke="#fff" stroke-width="2"/>
        <circle cx="13" cy="9" r="2" fill="#fff"/>
        <polyline points="6,17 2,24 24,24 20,17" fill="none" stroke="#fff" stroke-width="2"/>
      </svg>
      <span>2204/56 marlow street,<br>fenwick qld 4102</span>
    </li>
  </ul>
</div>
</body>
</html>
```